Landscape design build company door flyer

I would like this flyer to convey a high-level of professionalism for a company that is excellent with communication with their clients as well as a company that does incredible installations

Went on vacation/holiday

```html
<!DOCTYPE html>
<html lang="en">
<head>
<meta charset="UTF-8">
<title>Cedar Ridge Builders – Outdoor Living Spaces Flyer</title>
<link rel="stylesheet" href="https://fonts.googleapis.com/css2?family=Poppins:wght@400;500;600;700;800&display=swap">
<style>
  :root{
    --navy:#0d2b40;
    --stone:#c9c9c9;
    --paper:#f1f1f1;
    --ink:#111111;
    --rule:#9a9a9a;
    --backdrop:#808080;
    --white:#ffffff;
  }
  *{margin:0;padding:0;box-sizing:border-box;}
  html,body{width:1200px;height:933px;overflow:hidden;background:var(--backdrop);font-family:"Poppins",sans-serif;}
  .flyer{position:absolute;left:267px;top:38px;width:665px;height:856px;background:var(--paper);overflow:hidden;}
  .flyer-shapes{position:absolute;left:0;top:0;width:665px;height:856px;}
  .brand{position:absolute;left:0;top:58px;width:262px;text-align:center;color:var(--navy);}
  .brand-mark{display:block;width:34px;height:34px;border-radius:50%;background:var(--navy);margin:0 auto 10px;}
  .brand-name{font-weight:600;font-size:15px;letter-spacing:.5px;line-height:1.1;}
  .brand-tagline{font-weight:600;font-size:7px;letter-spacing:.3px;margin-top:2px;}
  .headline{position:absolute;left:30px;top:168px;color:var(--white);font-weight:700;font-size:42px;line-height:48px;letter-spacing:-.5px;text-transform:uppercase;}
  .section-title{position:absolute;top:410px;font-weight:800;font-size:19px;color:var(--ink);letter-spacing:-.2px;}
  .section-title::after{content:"";display:block;width:58px;height:3px;background:var(--rule);margin-top:3px;}
  .about-title{left:30px;}
  .services-title{left:366px;}
  .about-text{position:absolute;left:30px;top:454px;width:282px;font-size:10.4px;line-height:12.7px;letter-spacing:.2px;text-align:justify;color:var(--ink);hyphens:auto;}
  .services-list{position:absolute;left:366px;top:455px;list-style:none;}
  .services-list li{display:flex;align-items:center;height:18px;font-size:12px;font-weight:500;color:var(--ink);}
  .services-list svg{width:11px;height:11px;margin-right:13px;flex:none;}
  .works-rule{position:absolute;left:0;top:613px;width:665px;height:2px;background:var(--navy);}
  .works-label{position:absolute;left:236px;top:599px;width:188px;height:26px;background:var(--navy);color:var(--white);font-weight:700;font-size:15px;line-height:26px;text-align:center;}
  .work{position:absolute;top:637px;width:180px;height:98px;}
  .work-deck{left:34px;background:linear-gradient(180deg,#4f7a3a 0%,#6a8c4a 35%,#8a4a32 60%,#6e3b28 100%);}
  .work-pool{left:239px;background:linear-gradient(135deg,#4d5b4a 0%,#cfd5d8 30%,#5ec8c4 50%,#c7ccd0 70%,#e3e6e8 100%);}
  .work-firepit{left:444px;background:linear-gradient(180deg,#2b2f33 0%,#3d6d8c 25%,#5a4a3c 55%,#3a302a 100%);}
  .phone{position:absolute;left:42px;top:790px;display:flex;align-items:center;color:var(--white);font-weight:700;font-size:38px;letter-spacing:-.8px;}
  .phone svg{width:24px;height:28px;margin-right:11px;}
  .contact-list{position:absolute;left:442px;top:787px;list-style:none;color:var(--navy);}
  .contact-list li{display:flex;align-items:center;height:22px;font-size:12.5px;font-weight:500;}
  .contact-list svg{width:14px;height:14px;margin-right:11px;flex:none;}
</style>
</head>
<body>
<main class="flyer">
  <svg class="flyer-shapes" viewBox="0 0 665 856">
    <defs>
      <linearGradient id="heroTones" x1="0" y1="0" x2="1" y2="1">
        <stop offset="0" stop-color="#5f8a3e"/>
        <stop offset=".35" stop-color="#5d6a72"/>
        <stop offset=".7" stop-color="#6b6e70"/>
        <stop offset="1" stop-color="#4a3428"/>
      </linearGradient>
    </defs>
    <rect class="top-panel" x="0" y="0" width="665" height="402" fill="var(--stone)"/>
    <polygon role="img" aria-label="Aerial photo of a two-storey house with a new paver driveway, steps and planting beds" points="307,0 665,0 665,402 200,402 258,136" fill="url(#heroTones)"/>
    <polygon class="headline-panel" points="0,136 312,136 444,402 0,402" fill="var(--navy)"/>
    <polygon class="footer-contact-panel" points="406,764 665,764 665,856 369,856" fill="var(--stone)"/>
    <polygon class="footer-phone-panel" points="0,776 401,776 369,856 0,856" fill="var(--navy)"/>
  </svg>

  <div class="brand">
    <span class="brand-mark"></span>
    <div class="brand-name">CEDAR RIDGE BUILDERS</div>
    <div class="brand-tagline">OUTDOOR LIVING SPACES</div>
  </div>

  <h1 class="headline">Let’s create<br>your dream<br>outdoor<br>living space!</h1>

  <h2 class="section-title about-title">ABOUT US</h2>
  <p class="about-text">Discover the endless possibilities for your outdoor space with The Cedar Ridge Builders Team. Our team of skilled artisans is dedicated to turning your outdoor space into a breathtaking oasis that you’ll love coming home to. Whether it’s a cozy patio for intimate gatherings, a sprawling deck to host memorable parties, or a custom paver driveway that adds instant curb appeal, our high-quality craftsmanship ensures stunning results that exceed your expectations.</p>

  <h2 class="section-title services-title">OUR SERVICES</h2>
  <ul class="services-list">
    <li><svg viewBox="0 0 12 12"><circle cx="6" cy="6" r="6" fill="var(--navy)"/><path d="M3.3 6.2l1.8 1.8 3.6-3.8" fill="none" stroke="#fff" stroke-width="1.5"/></svg>Paver Patios</li>
    <li><svg viewBox="0 0 12 12"><circle cx="6" cy="6" r="6" fill="var(--navy)"/><path d="M3.3 6.2l1.8 1.8 3.6-3.8" fill="none" stroke="#fff" stroke-width="1.5"/></svg>Paver Driveways</li>
    <li><svg viewBox="0 0 12 12"><circle cx="6" cy="6" r="6" fill="var(--navy)"/><path d="M3.3 6.2l1.8 1.8 3.6-3.8" fill="none" stroke="#fff" stroke-width="1.5"/></svg>Retaining Walls</li>
    <li><svg viewBox="0 0 12 12"><circle cx="6" cy="6" r="6" fill="var(--navy)"/><path d="M3.3 6.2l1.8 1.8 3.6-3.8" fill="none" stroke="#fff" stroke-width="1.5"/></svg>Decks &amp; Railings</li>
    <li><svg viewBox="0 0 12 12"><circle cx="6" cy="6" r="6" fill="var(--navy)"/><path d="M3.3 6.2l1.8 1.8 3.6-3.8" fill="none" stroke="#fff" stroke-width="1.5"/></svg>Pools</li>
    <li><svg viewBox="0 0 12 12"><circle cx="6" cy="6" r="6" fill="var(--navy)"/><path d="M3.3 6.2l1.8 1.8 3.6-3.8" fill="none" stroke="#fff" stroke-width="1.5"/></svg>Outdoor Lighting</li>
    <li><svg viewBox="0 0 12 12"><circle cx="6" cy="6" r="6" fill="var(--navy)"/><path d="M3.3 6.2l1.8 1.8 3.6-3.8" fill="none" stroke="#fff" stroke-width="1.5"/></svg>Firepits &amp; Fireplaces</li>
  </ul>

  <div class="works-rule"></div>
  <div class="works-label">OUR WORKS</div>
  <div class="work work-deck" role="img" aria-label="Wooden deck with pergola and patio chairs among trees"></div>
  <div class="work work-pool" role="img" aria-label="Aerial view of a small pool framed by white decking"></div>
  <div class="work work-firepit" role="img" aria-label="Evening patio with lit fire pit, curved seating and pool"></div>

  <div class="phone">
    <svg viewBox="0 0 24 28"><path d="M5 1.5l4 .5 2 6-3 2.5c1.5 4 4 7.5 7.5 9.5l3-2.5 5.5 3-.5 4.5c-1 1.5-3 2.5-5 2C9 24.5 2.5 16 1.5 6.5 1.5 4 3 2.5 5 1.5z" fill="var(--white)"/></svg>
    206-555-0148
  </div>

  <ul class="contact-list">
    <li><svg viewBox="0 0 14 14"><rect x="0.5" y="2.5" width="13" height="9" fill="var(--navy)"/><path d="M1 3.2l6 4.3 6-4.3" fill="none" stroke="var(--stone)" stroke-width="1.2"/></svg>info@cedarridgebuilders.com</li>
    <li><svg viewBox="0 0 14 14" fill="none" stroke="var(--navy)" stroke-width="1"><circle cx="7" cy="7" r="6"/><ellipse cx="7" cy="7" rx="2.6" ry="6"/><path d="M1 7h12"/></svg>www.cedarridgebuilders.com</li>
  </ul>
</main>
</body>
</html>
```